Coastal Learner Bureau business cards

Australian company about to start offering its services. We recruit international students to come to study English, vocational education and postgraduate courses in Australia. We help them find the institution and select the right city they want to come to Australia. We are a young, online oriented and supportive agency. Our clients are between 18 and 35 years old, mainly University students, young professionals or people with work experience. We provide much more information that any other agency offer. We administrate a Facebook group with more than 11.000 members that daily ask questions about general information when coming to Australia, while they are here and even after they leave the country

Target Market(s)

International students from South America, Central America and Europe

Industry/Entity Type

Student

Contact Information for Business Card

Tomas Bilbrea
Managing Director
tomas@kelvarin.com.au
www.kelvoria.com.au
+61 491058264
Port Wendell, Australia

Font styles to use
Serif
Sans Serif

Colors

Designer to choose colors to be used in the design.

Requirements
Must have
• Horizontal design
• Standard business card size and shape. If font uses green or yellow colours, they will have to match the ones from the logo
Nice to have
• UPDATE: Use the contents of the green image to design one of the card sides. Use our logo in the background of that side as watermark.
• Passport image, or immigration stamps. A picture of the Yarra River (from Melbourne) would be cool as well.
Should not have
• Non-standard business card size and shape
• Not black as the background colour of any sides as we are not a VIP agency or a hight class service. We are orientes to young people and they like colours, pictures, something attractive.
• Vertical design
• NO YELLOW or BLACK AS THE BACKGROUND COLOUR OF ANY SIDE OF THE BIZ CARD

```html
<!DOCTYPE html>
<html lang="en">
<head>
<meta charset="utf-8">
<title>Coastal Learner Bureau business cards</title>
<link href="https://fonts.googleapis.com/css2?family=Poppins:wght@400;500;600;700&display=swap" rel="stylesheet">
<style>
  :root {
    --paper: #eeece6;
    --brand-green: #0f6744;
    --brand-yellow: #e6b922;
    --white: #ffffff;
    --ink: #1f2a24;
    --night-top: #2a3850;
    --night-bottom: #3b4a5c;
  }
  * { margin: 0; padding: 0; box-sizing: border-box; }
  html, body {
    width: 1200px; height: 929px; overflow: hidden;
    background: var(--paper);
    font-family: "Poppins", sans-serif;
  }
  .card {
    position: absolute; left: 290px;
    width: 620px; height: 354px;
    overflow: hidden;
    box-shadow: 0 6px 18px rgba(0,0,0,0.18);
  }
  .card-front { top: 70px; }
  .card-back { top: 495px; background: var(--white); }

  .river-photo {
    position: absolute; inset: 0;
    background: linear-gradient(180deg, var(--night-top) 0%, #4a5668 45%, var(--night-bottom) 100%);
  }
  .front-brand {
    position: absolute; left: 0; right: 0; top: 128px;
    text-align: center;
    color: var(--white); font-weight: 600; font-size: 54px; letter-spacing: 1px;
  }
  .tagline {
    position: absolute; left: 0; right: 0; top: 262px;
    text-align: center; color: var(--white); font-size: 13px; font-weight: 500;
  }

  .wave { position: absolute; inset: 0; }
  .back-brand {
    position: absolute; left: 42px; top: 58px;
    display: flex; align-items: center; gap: 10px;
    color: var(--brand-green); font-weight: 600; font-size: 36px;
  }
  .back-brand .dot {
    width: 14px; height: 14px; border-radius: 50%; background: var(--brand-yellow);
  }
  .holder { position: absolute; left: 42px; top: 200px; }
  .holder-name {
    color: var(--brand-green); font-weight: 700; font-size: 21px; letter-spacing: 0.5px;
    text-transform: uppercase;
  }
  .holder-role { color: var(--ink); font-size: 14px; margin-top: -2px; }

  .contact {
    position: absolute; right: 34px; top: 118px;
    list-style: none; text-align: right;
    color: var(--white); font-size: 13px; line-height: 22px; letter-spacing: 0.3px;
  }
  .contact li { display: flex; justify-content: flex-end; align-items: center; gap: 8px; }
  .contact svg { width: 12px; height: 12px; flex: none; }
  .contact .no-icon { padding-right: 20px; }
  .contact .accent { color: var(--brand-yellow); }
</style>
</head>
<body>

<section class="card card-front">
  <div class="river-photo" role="img" aria-label="Photograph of a city river at dusk with a skyline and trees along the banks"></div>
  <div class="front-brand">Kelvoria</div>
  <p class="tagline">Vamos contigo siempre!</p>
</section>

<section class="card card-back">
  <svg class="wave" viewBox="0 0 620 354" preserveAspectRatio="none" aria-hidden="true">
    <path d="M408 0 C318 10 326 200 246 268 C176 326 50 314 0 322 L0 354 L620 354 L620 0 Z" fill="var(--brand-yellow)"/>
    <path d="M424 0 C334 12 342 206 262 276 C192 336 60 330 0 338 L0 354 L620 354 L620 0 Z" fill="var(--white)"/>
    <path d="M432 0 C342 14 350 210 270 280 C200 340 64 336 0 344 L0 354 L620 354 L620 0 Z" fill="var(--brand-green)"/>
  </svg>

  <div class="back-brand"><span class="dot"></span>Kelvoria</div>

  <div class="holder">
    <p class="holder-name">Tomas Bilbrea</p>
    <p class="holder-role">Managing Director</p>
  </div>

  <ul class="contact">
    <li class="no-icon">Port Wendell, Australia</li>
    <li><span>+61 491058264</span>
      <svg viewBox="0 0 12 12"><rect x="3" y="1" width="6" height="10" rx="1" fill="none" stroke="var(--brand-yellow)" stroke-width="1.3"/></svg>
    </li>
    <li><span>tomas@kelvarin.com.au</span>
      <svg viewBox="0 0 12 12"><rect x="1" y="2.5" width="10" height="7" fill="var(--brand-yellow)"/><path d="M1 2.5 L6 6.5 L11 2.5" fill="none" stroke="var(--brand-green)" stroke-width="1"/></svg>
    </li>
    <li><span>www.<span class="accent">kelvoria.com</span>.au</span>
      <svg viewBox="0 0 12 12"><circle cx="5" cy="5" r="3.3" fill="none" stroke="var(--brand-yellow)" stroke-width="1.5"/><path d="M7.5 7.5 L11 11" stroke="var(--brand-yellow)" stroke-width="1.8"/></svg>
    </li>
  </ul>
</section>

</body>
</html>
```